Bikes for Dreams - Website Redesign

Create a professional website for a nonprofit; BikesforDreams.org
Please see boatsforelders.org and www.pedalsforhopes.org for the concept I am after.
The webpage should have a fun feel and should match the style of the company at www.pedalsforhopes.org. The pages to include are 'Home', 'About us' and 'Get Started'
Thank you and good luck!
Reason: i would like to see more designs.

```html
<!DOCTYPE html>
<html lang="en">
<head>
<meta charset="utf-8">
<title>Bikes for Dreams</title>
<link href="https://fonts.googleapis.com/css2?family=Montserrat:wght@400;600;700&family=Open+Sans:wght@400;600&display=swap" rel="stylesheet">
<style>
:root{
  --teal:#55c3b6;
  --teal-dark:#3fae a1;
  --teal-deep:#3aa89b;
  --teal-light:#bfe8e2;
  --sky:#d8f1ee;
  --red:#e8463b;
  --red-dark:#cf3a30;
  --ink:#2c3a40;
  --muted:#8a9499;
  --white:#ffffff;
  --grey:#f1f3f3;
  --line:#dfe4e5;
}
*{box-sizing:border-box;margin:0;padding:0}
html,body{width:1200px;height:3252px;overflow:hidden}
body{position:relative;font-family:"Open Sans",Arial,sans-serif;color:var(--ink);background:var(--white)}
.section{position:absolute;left:0;width:1200px;overflow:hidden}
h2.section-title{position:absolute;left:0;width:100%;text-align:center;font-family:"Montserrat",Arial,sans-serif;font-weight:600;font-size:38px;letter-spacing:1px}

/* hero */
.hero{top:0;height:600px;background:linear-gradient(180deg,var(--sky) 0%,var(--teal-light) 30%,var(--teal) 62%,var(--teal-deep) 100%)}
.brand{position:absolute;left:104px;top:38px;display:flex;align-items:center;gap:12px}
.brand-dot{width:22px;height:22px;border-radius:50%;background:var(--red)}
.brand-name{font-family:"Montserrat",Arial,sans-serif;font-weight:700;font-size:22px;color:var(--ink)}
.phone{position:absolute;left:700px;top:64px;display:flex;align-items:center;gap:10px;font-family:"Montserrat",Arial,sans-serif;font-weight:600;font-size:22px;color:var(--ink)}
.btn{display:inline-block;background:var(--red);color:var(--white);font-family:"Montserrat",Arial,sans-serif;font-weight:600;text-align:center;border-radius:3px}
.btn-top{position:absolute;left:930px;top:62px;width:165px;height:42px;line-height:42px;font-size:15px}
.nav{position:absolute;left:560px;top:120px;display:flex;gap:34px;font-family:"Montserrat",Arial,sans-serif;font-size:12px;font-weight:600;color:var(--ink)}
.hero-art{position:absolute;left:110px;top:170px;width:560px;height:340px;border-radius:8px;background:radial-gradient(ellipse at 50% 45%,#f3d9a4 0%,#7fd0c6 55%,rgba(85,195,182,0) 80%)}
.play{position:absolute;left:506px;top:200px;width:56px;height:56px;border-radius:50%;background:var(--red)}
.hero-title{position:absolute;left:120px;top:360px;width:580px;text-align:center;font-family:"Montserrat",Arial,sans-serif;font-weight:700;font-size:32px;color:var(--white);letter-spacing:1px}
.donate-card{position:absolute;left:820px;top:196px;width:300px;height:336px;background:var(--white);border-radius:4px;box-shadow:0 6px 18px rgba(0,0,0,.15);padding:26px 22px}
.donate-card h3{font-family:"Montserrat",Arial,sans-serif;font-weight:600;font-size:22px;text-align:center;margin-bottom:18px}
.field{height:34px;border:1px solid var(--line);border-radius:2px;margin-bottom:14px;font-size:11px;color:var(--muted);line-height:32px;padding-left:10px}
.btn-card{display:block;width:100%;height:36px;line-height:36px;font-size:13px}
.pager{position:absolute;left:1146px;top:236px;display:flex;flex-direction:column;gap:18px}
.pager span{width:12px;height:12px;border-radius:50%;border:2px solid var(--white)}
.pager span.on{background:var(--white)}

/* why */
.why{top:600px;height:600px;background:var(--white)}
.why h2{top:68px}
.reasons{position:absolute;top:192px;left:0;width:100%}
.reason{position:absolute;width:220px;text-align:center}
.reason .circle{width:124px;height:124px;border-radius:50%;background:var(--red);margin:0 auto 42px;display:flex;align-items:center;justify-content:center}
.reason p{font-family:"Montserrat",Arial,sans-serif;font-size:14px;font-weight:600;line-height:1.4}

/* about */
.about{top:1200px;height:440px;background:var(--teal)}
.about h2{top:90px;color:var(--white)}
.arrow{position:absolute;top:1362px}
.features{position:absolute;top:88px;left:0;width:100%}
.feature{position:absolute;top:200px;width:248px;text-align:center;color:var(--white)}
.feature .frame{height:184px;background:var(--white);border:4px solid var(--red);display:flex;align-items:center;justify-content:center}
.feature .art{width:110px;height:110px;border-radius:50%;background:radial-gradient(circle,#f7c84a 0%,#f2a43b 60%,#f0e6d6 100%)}
.feature h4{font-family:"Montserrat",Arial,sans-serif;font-size:15px;font-weight:600;margin-top:18px}
.feature p{font-size:11px;margin-top:6px;opacity:.9}

/* clients */
.clients{top:1640px;height:540px;background:linear-gradient(135deg,#f6f7f7,#e9eced)}
.clients h2{top:82px}
.avatars{position:absolute;top:170px;left:0;width:100%;display:flex;justify-content:center;align-items:center;gap:22px}
.avatar{width:90px;height:90px;border-radius:50%;background:linear-gradient(160deg,#e9785f,#b84434)}
.avatar.main{width:112px;height:112px;background:linear-gradient(160deg,#d9a88a,#6b3b2e)}
.quote{position:absolute;top:304px;left:250px;width:700px;text-align:center;font-size:13px;line-height:1.7;color:var(--muted);font-style:italic}
.quote-link{position:absolute;top:390px;width:100%;text-align:center;font-family:"Montserrat",Arial,sans-serif;font-size:12px;font-weight:600;color:var(--red)}
.dots{position:absolute;top:452px;width:100%;display:flex;justify-content:center;gap:8px}
.dots span{width:9px;height:9px;border-radius:50%;background:#a7dcd5}
.dots span.on{background:var(--teal)}

/* pickup */
.pickup{top:2180px;height:700px;background:var(--white)}
.monitor{position:absolute;left:260px;top:84px;width:680px;height:520px;background:#1e2226;border-radius:14px 14px 0 0;padding:22px}
.screen{width:100%;height:100%;background:var(--white);text-align:center;padding-top:40px}
.screen h3{font-family:"Montserrat",Arial,sans-serif;font-weight:600;font-size:26px}
.form-label{font-family:"Montserrat",Arial,sans-serif;font-size:10px;font-weight:600;color:var(--red);margin:22px 0 12px;letter-spacing:.5px}
.row{display:flex;gap:12px;justify-content:center;margin-bottom:12px}
.row .field{width:150px;margin:0;text-align:left}
.btn-submit{margin-top:26px;width:190px;height:36px;line-height:36px;font-size:12px}
.chin{position:absolute;left:260px;top:604px;width:680px;height:40px;background:linear-gradient(#e4e6e8,#c7cbce);border-radius:0 0 14px 14px}
.neck{position:absolute;left:540px;top:644px;width:120px;height:48px;background:linear-gradient(#c9cdd0,#e6e8ea)}
.base{position:absolute;left:480px;top:690px;width:240px;height:10px;background:#d3d6d8;border-radius:6px 6px 0 0}

/* footer */
.footer{top:2880px;height:372px;background:var(--teal);color:var(--white);text-align:center}
.social{position:absolute;top:92px;left:0;width:100%;display:flex;justify-content:center;gap:16px}
.social span{width:44px;height:44px;border-radius:50%;border:2px solid var(--white)}
.rule{position:absolute;top:178px;left:500px;width:200px;height:1px;background:rgba(255,255,255,.6)}
.foot-nav{position:absolute;top:216px;left:0;width:100%;display:flex;justify-content:center;gap:40px;font-family:"Montserrat",Arial,sans-serif;font-size:11px;font-weight:600}
.copy{position:absolute;top:266px;width:100%;font-size:11px;opacity:.85}
</style>
</head>
<body>

<section class="section hero">
  <div class="brand"><span class="brand-dot"></span><span class="brand-name">Bikes for Dreams</span></div>
  <div class="phone">
    <svg width="22" height="22" viewBox="0 0 24 24"><path fill="#2c3a40" d="M6.6 10.8a15.1 15.1 0 0 0 6.6 6.6l2.2-2.2c.3-.3.7-.4 1-.2 1.1.4 2.3.6 3.6.6.6 0 1 .4 1 1V20c0 .6-.4 1-1 1A17 17 0 0 1 3 4c0-.6.4-1 1-1h3.5c.6 0 1 .4 1 1 0 1.3.2 2.5.6 3.6.1.3 0 .7-.2 1z"/></svg>
    1-888-555-0142
  </div>
  <a class="btn btn-top">DONATE NOW!</a>
  <nav class="nav"><span>WHY DONATE YOUR BIKE</span><span>ABOUT OUR CHARITY</span><span>F.A.Q</span><span>BLOG</span></nav>
  <div class="hero-art" role="img" aria-label="Illustration of a smiling man holding a piggy bank in front of a house and car"></div>
  <svg class="play" viewBox="0 0 56 56"><circle cx="28" cy="28" r="28" fill="#e8463b"/><path d="M23 18 L38 28 L23 38 Z" fill="#fff"/></svg>
  <h1 class="hero-title">DONATE CAR TO CHARITY!</h1>
  <form class="donate-card">
    <h3>DONATE A CAR</h3>
    <div class="field">Enter Name</div>
    <div class="field">Enter Email</div>
    <div class="field">Phone Number</div>
    <div class="field">Vehicle Year &amp; Condition ▾</div>
    <a class="btn btn-card">DONATE NOW</a>
  </form>
  <div class="pager"><span></span><span class="on"></span><span></span><span></span></div>
</section>

<section class="section why">
  <h2 class="section-title">WHY DONATE A CAR</h2>
  <div class="reasons">
    <div class="reason" style="left:98px">
      <div class="circle"><svg width="60" height="40" viewBox="0 0 60 40"><rect x="4" y="14" width="34" height="14" rx="2" fill="#fff"/><path d="M38 16h10l8 8v4H38z" fill="#fff"/><circle cx="14" cy="32" r="5" fill="#fff"/><circle cx="46" cy="32" r="5" fill="#fff"/><path d="M8 14 L20 2" stroke="#fff" stroke-width="3"/></svg></div>
      <p>TOWING IS FREE</p>
    </div>
    <div class="reason" style="left:358px">
      <div class="circle"><svg width="56" height="56" viewBox="0 0 56 56"><circle cx="28" cy="28" r="24" fill="#fff"/><path d="M16 18c6-2 10 2 8 8s4 8 2 14M34 12c4 4 10 6 12 12" stroke="#e8463b" stroke-width="5" fill="none"/></svg></div>
      <p>DONATIONS ACCEPTED<br>NATIONWIDE</p>
    </div>
    <div class="reason" style="left:618px">
      <div class="circle"><svg width="60" height="44" viewBox="0 0 60 44"><path d="M10 18l6-12h28l6 12h4v16H6V18z" fill="#fff"/><rect x="18" y="10" width="24" height="8" fill="#e8463b"/><rect x="8" y="34" width="10" height="8" fill="#fff"/><rect x="42" y="34" width="10" height="8" fill="#fff"/><circle cx="15" cy="26" r="3" fill="#e8463b"/><circle cx="45" cy="26" r="3" fill="#e8463b"/></svg></div>
      <p>ALL VEHICLES TYPE<br>WELCOME</p>
    </div>
    <div class="reason" style="left:878px">
      <div class="circle"><svg width="44" height="56" viewBox="0 0 44 56"><path d="M4 2h26l10 10v42H4z" fill="#fff"/><text x="22" y="36" text-anchor="middle" font-family="Montserrat,Arial,sans-serif" font-size="13" font-weight="700" fill="#e8463b">TAX</text></svg></div>
      <p>TAX DEDUCTIBLE</p>
    </div>
  </div>
</section>

<section class="section about">
  <h2 class="section-title">ABOUT THE CHARITY!</h2>
  <div class="features">
    <div class="feature" style="left:100px;top:0"><div class="frame"><div class="art" role="img" aria-label="Illustration of a tow truck"></div></div><h4>FREE LOCAL TOWING</h4><p>Towing is free, no matter the condition</p></div>
    <div class="feature" style="left:356px;top:0"><div class="frame"><div class="art" role="img" aria-label="Illustration of a fast pickup timer"></div></div><h4>FAST PICKUP</h4><p>Same day or next day pickup</p></div>
    <div class="feature" style="left:612px;top:0"><div class="frame"><div class="art" role="img" aria-label="Illustration of a tax deduction form"></div></div><h4>INCOME TAX DEDUCTION</h4><p>Your donation may be fully tax deductible</p></div>
    <div class="feature" style="left:868px;top:0"><div class="frame"><div class="art" role="img" aria-label="Illustration of paperwork notes"></div></div><h4>NO PAPERWORK HASSLES</h4><p>We take care of all the paperwork for you</p></div>
  </div>
  <svg class="arrow" style="left:54px;top:162px" width="16" height="26" viewBox="0 0 16 26"><path d="M13 2 L3 13 L13 24" stroke="#fff" stroke-width="3" fill="none"/></svg>
  <svg class="arrow" style="left:1128px;top:162px" width="16" height="26" viewBox="0 0 16 26"><path d="M3 2 L13 13 L3 24" stroke="#fff" stroke-width="3" fill="none"/></svg>
</section>

<section class="section clients">
  <h2 class="section-title">HAPPY CLIENTS SAY</h2>
  <div class="avatars">
    <div class="avatar" role="img" aria-label="Client portrait"></div>
    <div class="avatar main" role="img" aria-label="Featured client portrait"></div>
    <div class="avatar" role="img" aria-label="Client portrait"></div>
  </div>
  <p class="quote">“Donating my old vehicle was quick and simple. The team picked it up the very next day, handled every form for me, and kept me informed at each step. Knowing it helps someone's dream come true makes it even better. I would gladly recommend this charity to my friends and family.”</p>
  <div class="quote-link">DONOR FAMILY, OREGON</div>
  <div class="dots"><span class="on"></span><span></span><span></span></div>
</section>

<section class="section pickup">
  <div class="monitor">
    <form class="screen">
      <h3>DONATION PICK UP FORM</h3>
      <div class="form-label">● CONTACT INFORMATION</div>
      <div class="row"><div class="field">First Name</div><div class="field">Last Name</div><div class="field">Zip Code</div></div>
      <div class="row"><div class="field">Email Address</div><div class="field">Day Phone</div></div>
      <div class="form-label">● VEHICLE DONATION INFORMATION</div>
      <div class="row"><div class="field">Year of Vehicle</div><div class="field">Make of Vehicle</div><div class="field">Model of Vehicle</div></div>
      <a class="btn btn-submit">SUBMIT APPLICATION</a>
    </form>
  </div>
  <div class="chin"></div>
  <div class="neck"></div>
  <div class="base"></div>
</section>

<footer class="section footer">
  <div class="social"><span></span><span></span><span></span><span></span><span></span></div>
  <div class="rule"></div>
  <nav class="foot-nav"><span>HOME</span><span>WHY DONATE YOUR BIKE</span><span>ABOUT OUR CHARITY</span><span>F.A.Q</span><span>BLOG</span><span>CONTACT</span></nav>
  <p class="copy">© Copyright 2017 Bikes for Dreams. All rights reserved.</p>
</footer>

</body>
</html>
```